TALMORK

The business want a professional looking business card. We have a scetch we will add but want the extra upgrade, and would like more suggestions for variations of our business cards.

```html
<!DOCTYPE html>
<html lang="en">
<head>
<meta charset="utf-8">
<title>Talmork – Business Card</title>
<link href="https://fonts.googleapis.com/css2?family=Federo&family=Poppins:wght@400&display=swap" rel="stylesheet">
<style>
  :root {
    --backdrop: #d6d6d6;
    --card-light: #f0f0f0;
    --gold-light: #d9bf62;
    --gold-mid: #b58f3e;
    --gold-dark: #9a6a22;
    --rule-gold: #b08a3c;
    --ink: #505050;
    --ink-dark: #1f3440;
    --white: #f4f1ea;
    --back-top: #965d15;
    --back-upper: #8b5512;
    --back-bottom: #c0a04e;
  }
  * { margin: 0; padding: 0; box-sizing: border-box; }
  html, body { width: 1200px; height: 1200px; overflow: hidden; }
  body { background: var(--backdrop); position: relative; font-family: "Poppins", sans-serif; }

  .card { position: absolute; left: 234px; width: 732px; height: 418px; }
  .card-front { top: 153px; background: var(--card-light); }
  .card-back {
    top: 629px;
    background: linear-gradient(180deg, var(--back-top) 0%, var(--back-upper) 20%, #a37a31 55%, var(--back-bottom) 100%);
  }

  .gold-text {
    background: linear-gradient(180deg, var(--gold-light), var(--gold-dark));
    -webkit-background-clip: text; background-clip: text; color: transparent;
  }

  .holder-icon { position: absolute; left: 53px; top: 69px; width: 24px; height: 24px; }
  .holder-name {
    position: absolute; left: 89px; top: 58px;
    font-family: "Federo", sans-serif; font-size: 41px; line-height: 1; letter-spacing: 0.5px;
  }
  .name-underline { position: absolute; left: 89px; top: 104px; width: 191px; height: 1px; background: var(--ink-dark); }
  .holder-role { position: absolute; left: 89px; top: 111px; font-size: 12px; color: var(--ink); }
  .holder-fullname { position: absolute; left: 89px; top: 127px; font-size: 16px; color: var(--ink); }

  .divider-bold { position: absolute; left: 53px; top: 162px; width: 304px; height: 7px; background: var(--rule-gold); }
  .divider-thin { position: absolute; left: 357px; top: 165px; width: 322px; height: 2px; background: var(--rule-gold); }

  .contact-list { position: absolute; left: 53px; top: 233px; list-style: none; }
  .contact-item { display: flex; align-items: center; height: 45px; font-size: 20px; color: var(--ink); }
  .contact-item svg { width: 20px; height: 20px; margin-right: 16px; flex: none; }

  .front-mark {
    position: absolute; left: 500px; top: 258px; display: flex; align-items: center; gap: 10px;
    font-family: "Federo", sans-serif; font-size: 30px; letter-spacing: 3px; color: var(--gold-mid);
  }
  .front-mark .dot { width: 14px; height: 14px; border-radius: 50%; background: var(--gold-mid); }

  .back-mark {
    position: absolute; left: 0; right: 0; top: 150px; display: flex; flex-direction: column; align-items: center;
  }
  .back-mark .dot { width: 34px; height: 34px; border-radius: 50%; background: var(--white); margin-bottom: 36px; }
  .back-wordmark {
    font-family: "Federo", sans-serif; font-size: 46px; line-height: 1; letter-spacing: 14px;
    color: var(--white); padding-left: 14px;
  }
  .back-since { margin-top: 12px; font-size: 12px; letter-spacing: 6px; color: var(--white); padding-left: 6px; }
</style>
</head>
<body>
  <section class="card card-front">
    <svg class="holder-icon" viewBox="0 0 24 24" aria-hidden="true">
      <defs><linearGradient id="goldFill" x1="0" y1="0" x2="1" y2="1"><stop offset="0" stop-color="#d9bf62"/><stop offset="1" stop-color="#a77a2e"/></linearGradient></defs>
      <circle cx="12" cy="6" r="5" fill="url(#goldFill)"/>
      <path d="M1 24 C1 15 6 12.5 12 12.5 S23 15 23 24 Z" fill="url(#goldFill)"/>
    </svg>
    <h1 class="holder-name gold-text">TALMORK BRANDVIK</h1>
    <div class="name-underline"></div>
    <p class="holder-role">CEO &amp; Founder</p>
    <p class="holder-fullname">Ola Henrik Brandvik</p>
    <div class="divider-bold"></div>
    <div class="divider-thin"></div>

    <ul class="contact-list">
      <li class="contact-item">
        <svg viewBox="0 0 24 24" aria-hidden="true"><path fill="#b58f3e" d="M5 2l4 1 1.5 5-2.5 2c1.3 2.8 3.2 4.7 6 6l2-2.5 5 1.5 1 4c0 1.5-1.5 3-3 3C10 22 2 14 2 5c0-1.5 1.5-3 3-3z"/></svg>
        +004790455172
      </li>
      <li class="contact-item">
        <svg viewBox="0 0 24 24" aria-hidden="true"><rect x="1" y="5" width="22" height="14" fill="#c9a64f"/><path d="M1 5l11 8 11-8M1 19l8-7M23 19l-8-7" fill="none" stroke="#f0f0f0" stroke-width="1.3"/></svg>
        talmork.llc@mailbox.com
      </li>
      <li class="contact-item">
        <svg viewBox="0 0 24 24" aria-hidden="true"><g fill="none" stroke="#b58f3e" stroke-width="1.4"><circle cx="12" cy="12" r="10"/><ellipse cx="12" cy="12" rx="4.5" ry="10"/><path d="M2 12h20M12 2v20M4 7h16M4 17h16"/></g></svg>
        www.talmork.llc
      </li>
    </ul>

    <div class="front-mark"><span class="dot"></span>TALMORK</div>
  </section>

  <section class="card card-back">
    <div class="back-mark">
      <span class="dot"></span>
      <div class="back-wordmark">TALMORK</div>
      <div class="back-since">SINCE 2026</div>
    </div>
  </section>
</body>
</html>
```